We need a new business card that reflects who we are. Professional, classy, modern, and service ori

We need a business card design for a window coverings design company in Kansas City called Bright Lane Interiors. We offer professional, modern, and high quality window covering products. We are looking to portray an image of a big, national franchise. We are a 5 location (with showrooms) business with 10 professional designers and 4 professional installers. These cards will be used with Thank you cards, given to realtors, and asked for referrals with.

Target Market(s)

Kansas City

Industry/Entity Type

Business

Contact Information for Business Card

We would like our card to look clean and simple on the front, featuring our logo and Marlow Fenwick's. Our designers' phone numbers and emails should be displayed as well as their title.

Font styles to use
Sans Serif

Colors

Designer to choose colors to be used in the design.

Requirements
Must have
• Front - Logos, name, phone number, email address
• Back - Showroom locations, social media? Appt date/time?
Nice to have
• I would like a clean and modern look (not contemporary. I like a white background, but I am open to ideas. Looking for a "National chain" look for a small business.
Should not have
• Too much busyness.

```html
<!DOCTYPE html>
<html lang="en">
<head>
<meta charset="utf-8">
<title>Bright Lane Interiors – Business Card</title>
<link rel="stylesheet" href="https://fonts.googleapis.com/css2?family=Lato:wght@400;700&family=Tinos:wght@400;700&display=swap">
<style>
  :root {
    --stage: #1f1f1f;
    --card: #ffffff;
    --brand-red: #c84046;
    --brand-grey: #939598;
    --ink: #111111;
    --partner-orange: #ee8a22;
    --partner-slate: #4b5560;
    --rule: #b9bbbe;
  }
  * { margin: 0; padding: 0; box-sizing: border-box; }
  html, body { width: 1200px; height: 900px; overflow: hidden; background: var(--stage); }
  .stage { position: relative; width: 1200px; height: 900px; }
  .card {
    position: absolute; top: 306px; width: 440px; height: 271px;
    background: var(--card);
    box-shadow: 2px 3px 6px rgba(0,0,0,.55);
    overflow: hidden;
  }
  .card--front { left: 149px; }
  .card--back { left: 608px; }

  .serif { font-family: "Tinos", "Times New Roman", serif; }
  .sans { font-family: "Lato", Arial, sans-serif; }

  /* front */
  .brand-block { position: absolute; left: 200px; top: 18px; width: 218px; text-align: center; }
  .brand-mark { display: block; width: 58px; height: 58px; margin: 0 auto 10px; background: var(--brand-red); }
  .brand-name { font-family: "Tinos", "Times New Roman", serif; font-size: 19px; color: var(--ink); line-height: 1; white-space: nowrap; }
  .brand-tagline { font-family: "Tinos", "Times New Roman", serif; font-size: 11.5px; color: var(--ink); margin-top: 5px; white-space: nowrap; }

  .person { position: absolute; left: 25px; top: 160px; }
  .person-name { font-family: "Tinos", "Times New Roman", serif; font-weight: 700; font-size: 16px; letter-spacing: .2px; }
  .person-name .first { color: var(--brand-red); }
  .person-name .last { color: var(--ink); }
  .person-title { font-family: "Lato", Arial, sans-serif; font-size: 12.5px; color: var(--ink); margin-top: 1px; }

  .contact { position: absolute; left: 24px; top: 207px; font-family: "Lato", Arial, sans-serif; font-size: 12.5px; color: var(--ink); list-style: none; }
  .contact li { display: flex; align-items: center; gap: 4px; height: 16px; }
  .contact svg { width: 10px; height: 10px; fill: var(--brand-red); }

  .partner { position: absolute; left: 318px; top: 147px; width: 104px; text-align: center; }
  .partner-dot { display: block; width: 57px; height: 57px; border-radius: 50%; background: var(--partner-orange); margin: 0 auto 4px; }
  .partner-name { font-family: "Lato", Arial, sans-serif; font-weight: 700; font-size: 12px; color: var(--partner-slate); white-space: nowrap; }
  .partner-sub { font-family: "Lato", Arial, sans-serif; font-size: 11px; color: var(--partner-slate); margin-top: 1px; }

  .front-bar { position: absolute; left: 0; bottom: 0; width: 100%; height: 19px; display: flex; }
  .front-bar .grey { background: var(--brand-grey); width: 103px; }
  .front-bar .red { background: var(--brand-red); width: 231px; }
  .front-bar .grey-end { background: var(--brand-grey); flex: 1; }

  /* back */
  .back-brand { position: absolute; top: 36px; left: 0; width: 100%; text-align: center; }
  .back-brand .brand-name { font-size: 20px; }
  .back-brand .brand-tagline { font-size: 11.5px; margin-top: 4px; }

  .locations { position: absolute; top: 99px; left: 0; width: 100%; height: 70px; background: var(--brand-red); color: #fff; text-align: center; font-family: "Lato", Arial, sans-serif; }
  .locations-title { font-size: 12.5px; font-weight: 700; letter-spacing: .3px; margin-top: 14px; }
  .locations-list { list-style: none; display: flex; justify-content: center; align-items: center; margin-top: 13px; font-size: 12.5px; }
  .locations-list li + li::before { content: ""; display: inline-block; width: 5px; height: 5px; border-radius: 50%; background: #fff; margin: 0 10px 2px; vertical-align: middle; }

  .social { position: absolute; top: 169px; left: 0; width: 100%; height: 45px; background: var(--brand-grey); }
  .social-rule { position: absolute; top: 23px; left: 28px; right: 28px; height: 1px; background: var(--rule); }
  .social-icons { position: absolute; top: 15px; left: 184px; display: flex; gap: 3px; }
  .social-icons span { width: 16px; height: 16px; border-radius: 50%; background: #fff; display: block; }

  .appointment { position: absolute; top: 231px; left: 0; width: 100%; text-align: center; font-family: "Lato", Arial, sans-serif; font-size: 12.5px; color: var(--ink); letter-spacing: .2px; }
  .appointment .field + .field { margin-left: 6px; }
</style>
</head>
<body>
<main class="stage">

  <section class="card card--front" aria-label="Business card front">
    <div class="brand-block">
      <span class="brand-mark" aria-hidden="true"></span>
      <div class="brand-name">Bright Lane Interiors</div>
      <div class="brand-tagline">Blinds, Shades, Shutters, Draperies &amp; Decor</div>
    </div>

    <div class="person">
      <div class="person-name"><span class="first">DANIEL</span> <span class="last">REEVES</span></div>
      <div class="person-title">Managing Director</div>
    </div>

    <ul class="contact">
      <li>
        <svg viewBox="0 0 10 10" aria-hidden="true"><path d="M1 4c0-2 1.5-3 4-3s4 1 4 3l-2 .5L6.5 3h-3L3 4.5zM2.5 5h5l1 4h-7z"/></svg>
        444 555 0192
      </li>
      <li>
        <svg viewBox="0 0 10 10" aria-hidden="true"><path d="M0 2h10v6H0zM.8 2.6 5 5.6l4.2-3"/><path d="M.8 2.6 5 5.6l4.2-3" fill="none" stroke="#fff" stroke-width=".9"/></svg>
        info@brightlaneinteriors.com
      </li>
    </ul>

    <div class="partner">
      <span class="partner-dot" aria-hidden="true"></span>
      <div class="partner-name">Marlow Fenwick</div>
      <div class="partner-sub">Gallery</div>
    </div>

    <div class="front-bar" aria-hidden="true">
      <span class="grey"></span><span class="red"></span><span class="grey-end"></span>
    </div>
  </section>

  <section class="card card--back" aria-label="Business card back">
    <div class="back-brand">
      <div class="brand-name">Bright Lane Interiors</div>
      <div class="brand-tagline">Blinds, Shades, Shutters, Draperies &amp; Decor</div>
    </div>

    <div class="locations">
      <div class="locations-title">SHOWROOM LOCATIONS</div>
      <ul class="locations-list">
        <li>Location 1</li><li>Location 2</li><li>Location 3</li><li>Location 4</li><li>Location 5</li>
      </ul>
    </div>

    <div class="social" aria-label="Social media links">
      <div class="social-rule"></div>
      <div class="social-icons"><span></span><span></span><span></span><span></span></div>
    </div>

    <div class="appointment">
      <span class="field">DATE___________________</span>
      <span class="field">TIME__________________</span>
    </div>
  </section>

</main>
</body>
</html>
```